New Business Card Design

We would like to refresh our business cards and make them look better. We are an IT company specialising in Cloud Services, IT Managed Services, software and hardware. I have attached a PSD of our current design. Also attached our logo.
Updates

I have uploaded all new logos in EPS format.

Can you please edit all designs to include a job title for Marcus Hollis, eg. General Manager

Industry/Entity Type

Software

Colors
ffffff

Requirements
Must have
• Please use white background.
Should not have
• Black background

```html
<!DOCTYPE html>
<html lang="en">
<head>
<meta charset="utf-8">
<title>Meridian Systems – Business Card</title>
<link href="https://fonts.googleapis.com/css2?family=Open+Sans:wght@400;600;700&display=swap" rel="stylesheet">
<style>
  :root {
    --page: #e9e9ee;
    --card: #ffffff;
    --ink: #2b2f33;
    --muted: #555a5f;
    --red: #c8372a;
  }
  * { margin: 0; padding: 0; box-sizing: border-box; }
  html, body {
    width: 1200px; height: 987px; overflow: hidden;
    background: var(--page);
    font-family: "Open Sans", Arial, sans-serif;
    color: var(--ink);
  }
  .canvas { position: relative; width: 1200px; height: 987px; }
  .card {
    position: absolute; left: 240px;
    width: 720px; height: 440px;
    background: var(--card);
    border-radius: 28px;
    box-shadow: 0 6px 20px rgba(0,0,0,0.12);
    overflow: hidden;
  }
  .card--back { top: 36px; }
  .card--front { top: 511px; }

  /* back face */
  .brand-block {
    position: absolute; left: 0; right: 0; top: 120px;
    display: flex; align-items: center; justify-content: center; gap: 22px;
  }
  .brand-dot {
    width: 56px; height: 56px; border-radius: 50%;
    background: var(--red); flex: none;
  }
  .brand-name {
    font-size: 58px; font-weight: 400; letter-spacing: 6px;
    color: var(--ink); line-height: 1; white-space: nowrap;
  }
  .tagline {
    position: absolute; left: 30px; right: 30px; top: 260px;
    font-size: 23px; line-height: 1.4; text-align: center;
    color: var(--muted);
  }
  .tagline span { display: block; white-space: nowrap; }

  /* front face */
  .accent-bar {
    position: absolute; left: 0; top: 36px;
    width: 10px; height: 52px; background: var(--red);
  }
  .person { position: absolute; left: 44px; top: 36px; }
  .person__name { font-size: 24px; font-weight: 700; color: var(--red); line-height: 1.1; }
  .person__title { font-size: 17px; color: var(--ink); margin-top: 2px; }
  .contacts { position: absolute; left: 44px; top: 160px; list-style: none; }
  .contacts li {
    display: flex; align-items: center; gap: 12px;
    font-size: 17px; color: var(--muted); margin-bottom: 12px;
  }
  .contacts svg { width: 18px; height: 18px; flex: none; }
  .website {
    position: absolute; left: 44px; top: 382px;
    font-size: 19px; letter-spacing: 2px; color: var(--muted);
    white-space: nowrap;
  }
  .front-brand {
    position: absolute; right: 44px; top: 300px;
    display: flex; align-items: center; gap: 16px;
  }
  .front-brand .brand-dot { width: 40px; height: 40px; }
  .front-brand .brand-name { font-size: 36px; letter-spacing: 3px; }
</style>
</head>
<body>
<main class="canvas">

  <section class="card card--back" aria-label="Card back">
    <div class="brand-block">
      <span class="brand-dot"></span>
      <span class="brand-name">meridian systems</span>
    </div>
    <p class="tagline">
      <span>We are an IT company specializing in Cloud Services</span>
      <span>IT Managed Services, software and hardware</span>
    </p>
  </section>

  <section class="card card--front" aria-label="Card front">
    <span class="accent-bar"></span>
    <div class="person">
      <p class="person__name">Marcus Hollis</p>
      <p class="person__title">General Manager</p>
    </div>
    <ul class="contacts">
      <li>
        <svg viewBox="0 0 20 20" aria-hidden="true"><circle cx="10" cy="10" r="9" fill="none" stroke="#c8372a" stroke-width="2"/><path d="M7 5c-1 1-1 3 1 6s4 4 5 4l1-2-2-1-1 1c-1-.5-2-2-2.5-3l1-1-1-2z" fill="#c8372a"/></svg>
        07 5550 1234
      </li>
      <li>
        <svg viewBox="0 0 20 20" aria-hidden="true"><rect x="5" y="1" width="10" height="18" rx="2" fill="#c8372a"/><rect x="7" y="4" width="6" height="8" fill="#fff"/><circle cx="10" cy="15.5" r="1.2" fill="#fff"/></svg>
        0400 555 018
      </li>
      <li>
        <svg viewBox="0 0 20 20" aria-hidden="true"><rect x="1" y="4" width="18" height="12" rx="2" fill="#c8372a"/><path d="M2 5l8 6 8-6" fill="none" stroke="#fff" stroke-width="1.6"/></svg>
        mhollis@meridiansys.com.au
      </li>
    </ul>
    <div class="front-brand">
      <span class="brand-dot"></span>
      <span class="brand-name">meridian systems</span>
    </div>
    <p class="website">www.meridiansys.com.au</p>
  </section>

</main>
</body>
</html>
```